Redesign of business card for Cedar Ridge Mechanical

We are looking for a new design for our business cards for Cedar Ridge Mechanical. We are a plumbing & HVAC construction company, operating on the West Coast of Canada and USA. Logo attached.
Industry/Entity Type
Construction - Plumbing & HVAC
Contact Information for Business Card
Name, address, phone numbers, email, website address
Look and feel
Each slider illustrates characteristics of the customer's brand and the style your logo design should communicate.

```html
<!DOCTYPE html>
<html lang="en">
<head>
<meta charset="UTF-8">
<title>Cedar Ridge Mechanical – Business Card</title>
<link rel="stylesheet" href="https://fonts.googleapis.com/css2?family=Montserrat:wght@400;600;700&display=swap">
<style>
  :root {
    --backdrop: #8b7a64;
    --card-white: #ffffff;
    --ink: #1a1a1a;
    --card-black: #111111;
    --gloss: #5a5a5a;
    --reverse: #ffffff;
  }
  * { margin: 0; padding: 0; box-sizing: border-box; }
  html, body { width: 900px; height: 1200px; overflow: hidden; }
  body {
    position: relative;
    background: var(--backdrop);
    font-family: "Montserrat", sans-serif;
    color: var(--ink);
  }
  .card {
    position: absolute;
    border-radius: 22px;
    overflow: hidden;
    box-shadow: 0 6px 14px rgba(0,0,0,0.35);
  }
  .card-front {
    left: 80px; top: 131px; width: 742px; height: 440px;
    background: var(--card-white);
  }
  .holder-name {
    position: absolute; left: 37px; top: 46px;
    font-size: 26px; font-weight: 700; letter-spacing: 0.2px;
  }
  .holder-title {
    position: absolute; left: 37px; top: 79px;
    font-size: 16px; font-weight: 400;
  }
  .address {
    position: absolute; left: 40px; top: 258px;
    font-size: 16px; line-height: 21px;
  }
  .contact-list {
    position: absolute; left: 38px; top: 329px;
    list-style: none; font-size: 16px;
  }
  .contact-list li {
    display: flex; align-items: center; gap: 11px;
    height: 20px; margin-bottom: 11px;
  }
  .contact-list svg { width: 16px; height: 16px; fill: var(--ink); flex: none; }
  .brand-lockup {
    position: absolute; left: 306px; top: 150px; width: 360px;
    display: flex; align-items: center; gap: 18px;
  }
  .brand-square {
    width: 62px; height: 62px; background: var(--ink); flex: none;
  }
  .brand-name {
    font-size: 30px; font-weight: 700; line-height: 36px;
    text-transform: uppercase; color: var(--ink);
  }
  .card-back {
    left: 78px; top: 638px; width: 744px; height: 452px;
    background: var(--card-black);
  }
  .back-texture {
    position: absolute; inset: 0;
    background: linear-gradient(120deg, var(--gloss) 0%, #2a2a2a 28%, var(--card-black) 48%, var(--card-black) 100%);
  }
  .back-lockup {
    position: absolute; left: 536px; top: 306px;
    display: flex; align-items: center; gap: 6px;
  }
  .back-square { width: 14px; height: 14px; background: var(--reverse); flex: none; }
  .back-name {
    font-size: 9px; font-weight: 700; line-height: 11px;
    text-transform: uppercase; color: var(--reverse); width: 80px;
  }
</style>
</head>
<body>
  <section class="card card-front">
    <h1 class="holder-name">Daniel Rourke</h1>
    <p class="holder-title">Managing Director</p>
    <address class="address" style="font-style:normal">428 Timber Hill Road<br>Kelso, WA 98626</address>
    <ul class="contact-list">
      <li>
        <svg viewBox="0 0 24 24" aria-hidden="true"><path d="M6.6 10.8a15.1 15.1 0 0 0 6.6 6.6l2.2-2.2a1 1 0 0 1 1-.25 11.4 11.4 0 0 0 3.6.57 1 1 0 0 1 1 1V20a1 1 0 0 1-1 1A17 17 0 0 1 3 4a1 1 0 0 1 1-1h3.5a1 1 0 0 1 1 1c0 1.25.2 2.45.57 3.6a1 1 0 0 1-.25 1z"/></svg>
        <span>555.301.4726</span>
      </li>
      <li>
        <svg viewBox="0 0 24 24" aria-hidden="true"><path d="M2 5h20v2l-10 6L2 7z M2 9l10 6 10-6v10H2z"/></svg>
        <span>info@cedarridgemechanical.com</span>
      </li>
      <li>
        <svg viewBox="0 0 24 24" aria-hidden="true"><path d="M12 2a10 10 0 1 0 0 20 10 10 0 0 0 0-20zm-1 17.9A8 8 0 0 1 4.1 10l4.9 5v1a2 2 0 0 0 2 2zm6.9-2.5A2 2 0 0 0 16 16h-1v-3a1 1 0 0 0-1-1H8v-2h2a1 1 0 0 0 1-1V7h2a2 2 0 0 0 2-2v-.4a8 8 0 0 1 2.9 12.8z"/></svg>
        <span>www.cedarridgemechanical.com</span>
      </li>
    </ul>
    <div class="brand-lockup">
      <span class="brand-square"></span>
      <span class="brand-name">Cedar Ridge<br>Mechanical</span>
    </div>
  </section>

  <section class="card card-back">
    <div class="back-texture" role="img" aria-label="Repeating glossy brand-mark pattern on black"></div>
    <div class="back-lockup">
      <span class="back-square"></span>
      <span class="back-name">Cedar Ridge Mechanical</span>
    </div>
  </section>
</body>
</html>
```